QVR business card

Need a business card for a company that provides instructional design and elearning development services. The website is here: http://quorvane.studio/

I'm attaching a current logo, as well as the old business card design. While I like to keep it clean, the old design is too simplistic for my liking. The only idea I want to reuse from the old design is placing industry jargon on the back of the card, just need a better way to present it. But if you have other ideas for the back--feel free to experiment.

Please use the colors complementary to the color we have on the website. Thank you!

```html
<!DOCTYPE html>
<html lang="en">
<head>
<meta charset="utf-8">
<title>QVR business card</title>
<link href="https://fonts.googleapis.com/css2?family=Montserrat:wght@500;600&family=Open+Sans:wght@400;600&family=Oswald:wght@400;500&display=swap" rel="stylesheet">
<style>
  :root {
    --teal: #17b1ae;
    --teal-deep: #0ea5a3;
    --lime: #c9d88e;
    --white: #ffffff;
    --ink: #3a3a3a;
    --backdrop: #e8e6e2;
  }
  html, body {
    margin: 0;
    width: 1200px;
    height: 1120px;
    overflow: hidden;
    background: var(--backdrop);
  }
  .canvas {
    position: relative;
    width: 1200px;
    height: 1120px;
  }
  .card {
    position: absolute;
    left: 160px;
    width: 880px;
    height: 503px;
    overflow: hidden;
    box-shadow: 0 6px 18px rgba(0,0,0,.12);
  }
  .card--front { top: 37px; background: var(--white); }
  .card--back  { top: 580px; background: var(--teal); }

  .card__shapes { position: absolute; inset: 0; }

  .brand {
    position: absolute;
    left: 72px;
    top: 118px;
    display: flex;
    align-items: center;
    gap: 16px;
  }
  .brand__dot {
    width: 44px;
    height: 44px;
    border-radius: 50%;
    background: var(--teal);
  }
  .brand__name {
    font-family: "Montserrat", sans-serif;
    font-weight: 600;
    font-size: 60px;
    line-height: 70px;
    letter-spacing: 4px;
    color: var(--teal);
  }

  .person {
    position: absolute;
    left: 72px;
    top: 248px;
    font-family: "Open Sans", sans-serif;
  }
  .person__name {
    margin: 0;
    font-weight: 600;
    font-size: 25px;
    color: var(--teal);
  }
  .person__role {
    margin: 4px 0 0;
    font-size: 24px;
    color: var(--ink);
  }

  .contact {
    position: absolute;
    right: 34px;
    bottom: 40px;
    margin: 0;
    padding: 0;
    list-style: none;
    text-align: right;
    font-family: "Open Sans", sans-serif;
    font-size: 19px;
    color: var(--white);
    line-height: 34px;
  }
  .contact__item { display: flex; justify-content: flex-end; align-items: center; gap: 8px; }
  .contact__icon { width: 16px; height: 16px; }

  .help {
    position: absolute;
    left: 52px;
    top: 46px;
    margin: 0;
    font-family: "Oswald", sans-serif;
    font-weight: 400;
    font-size: 100px;
    line-height: 102px;
    color: var(--white);
  }

  .services {
    position: absolute;
    left: 305px;
    top: 40px;
    margin: 0;
    padding: 0;
    list-style: none;
  }
  .services__item {
    display: flex;
    align-items: center;
    height: 70px;
  }
  .services__marker { width: 110px; height: 70px; flex: none; }
  .services__label {
    margin-left: 14px;
    font-family: "Oswald", sans-serif;
    font-weight: 500;
    font-size: 33px;
    letter-spacing: 1.5px;
    color: var(--white);
  }
</style>
</head>
<body>
<main class="canvas">

  <section class="card card--front" aria-label="Business card front">
    <svg class="card__shapes" width="880" height="503" viewBox="0 0 880 503" aria-hidden="true">
      <defs>
        <linearGradient id="cornerTint" x1="0" y1="0" x2="1" y2="0">
          <stop offset="0" stop-color="#17b1ae"/>
          <stop offset="0.6" stop-color="#17b1ae"/>
          <stop offset="1" stop-color="#c9d88e"/>
        </linearGradient>
        <linearGradient id="bandTint" x1="0" y1="0" x2="1" y2="0">
          <stop offset="0" stop-color="#c9d88e"/>
          <stop offset="0.4" stop-color="#17b1ae"/>
          <stop offset="1" stop-color="#17b1ae"/>
        </linearGradient>
      </defs>
      <polygon points="0,0 340,0 0,125" fill="url(#cornerTint)"/>
      <polygon points="330,503 880,215 880,503" fill="url(#bandTint)"/>
    </svg>

    <div class="brand">
      <span class="brand__dot"></span>
      <span class="brand__name">QVR</span>
    </div>

    <div class="person">
      <p class="person__name">Marten Holloway</p>
      <p class="person__role">Managing Director</p>
    </div>

    <ul class="contact">
      <li class="contact__item">
        <svg class="contact__icon" viewBox="0 0 16 16" aria-hidden="true"><circle cx="8" cy="8" r="7" fill="none" stroke="#fff" stroke-width="1.5"/><path d="M5.5 4.5l1.5 1.5-1 1c.5 1.2 1.3 2 2.5 2.5l1-1 1.5 1.5-1 1c-2.5-.5-4.5-2.5-5-5z" fill="#fff"/></svg>
        555-013-2740
      </li>
      <li class="contact__item">
        <svg class="contact__icon" viewBox="0 0 16 16" aria-hidden="true"><circle cx="8" cy="8" r="7" fill="none" stroke="#fff" stroke-width="1.5"/><ellipse cx="8" cy="8" rx="3" ry="7" fill="none" stroke="#fff" stroke-width="1.2"/><line x1="1" y1="8" x2="15" y2="8" stroke="#fff" stroke-width="1.2"/></svg>
        www.quorvane.studio
      </li>
      <li class="contact__item">
        <svg class="contact__icon" viewBox="0 0 16 16" aria-hidden="true"><circle cx="8" cy="8" r="7.5" fill="#fff"/><rect x="4" y="5.5" width="8" height="5.5" fill="#17b1ae"/><path d="M4 5.5l4 3 4-3" fill="none" stroke="#fff" stroke-width="1"/></svg>
        mholloway@quorvane.studio
      </li>
    </ul>
  </section>

  <section class="card card--back" aria-label="Business card back">
    <h2 class="help">HOW<br>CAN<br>WE<br>HELP?</h2>

    <ul class="services">
      <li class="services__item">
        <svg class="services__marker" viewBox="0 0 110 70" aria-hidden="true">
          <line x1="55" y1="55" x2="55" y2="70" stroke="#fff" stroke-width="1.5"/>
          <polygon points="55,15 100,35 55,55 10,35" fill="none" stroke="#fff" stroke-width="2"/>
          <rect x="49" y="27" width="12" height="16" rx="1.5" fill="none" stroke="#fff" stroke-width="1.5"/>
        </svg>
        <span class="services__label">MOBILE LEARNING SCORM</span>
      </li>
      <li class="services__item">
        <svg class="services__marker" viewBox="0 0 110 70" aria-hidden="true">
          <line x1="55" y1="0" x2="55" y2="15" stroke="#fff" stroke-width="1.5"/>
          <line x1="55" y1="55" x2="55" y2="70" stroke="#fff" stroke-width="1.5"/>
          <polygon points="55,15 100,35 55,55 10,35" fill="none" stroke="#fff" stroke-width="2"/>
          <rect x="46" y="28" width="18" height="12" fill="none" stroke="#fff" stroke-width="1.5"/>
          <line x1="55" y1="40" x2="55" y2="44" stroke="#fff" stroke-width="1.5"/>
        </svg>
        <span class="services__label">INSTRUCTIONAL DESIGN LMS</span>
      </li>
      <li class="services__item">
        <svg class="services__marker" viewBox="0 0 110 70" aria-hidden="true">
          <line x1="55" y1="0" x2="55" y2="15" stroke="#fff" stroke-width="1.5"/>
          <line x1="55" y1="55" x2="55" y2="70" stroke="#fff" stroke-width="1.5"/>
          <polygon points="55,15 100,35 55,55 10,35" fill="none" stroke="#fff" stroke-width="2"/>
          <rect x="48" y="28" width="14" height="14" fill="none" stroke="#fff" stroke-width="1.5"/>
        </svg>
        <span class="services__label">MOOCS ELEARNING HTML5</span>
      </li>
      <li class="services__item">
        <svg class="services__marker" viewBox="0 0 110 70" aria-hidden="true">
          <line x1="55" y1="0" x2="55" y2="15" stroke="#fff" stroke-width="1.5"/>
          <line x1="55" y1="55" x2="55" y2="70" stroke="#fff" stroke-width="1.5"/>
          <polygon points="55,15 100,35 55,55 10,35" fill="none" stroke="#fff" stroke-width="2"/>
          <circle cx="55" cy="33" r="5" fill="#fff"/>
          <rect x="53" y="38" width="4" height="4" fill="#fff"/>
        </svg>
        <span class="services__label">ADULT LEARNING THEORY</span>
      </li>
      <li class="services__item">
        <svg class="services__marker" viewBox="0 0 110 70" aria-hidden="true">
          <line x1="55" y1="0" x2="55" y2="15" stroke="#fff" stroke-width="1.5"/>
          <line x1="55" y1="55" x2="55" y2="70" stroke="#fff" stroke-width="1.5"/>
          <polygon points="55,15 100,35 55,55 10,35" fill="none" stroke="#fff" stroke-width="2"/>
          <circle cx="55" cy="33" r="5" fill="none" stroke="#fff" stroke-width="1.5"/>
          <rect x="53" y="38" width="4" height="4" fill="#fff"/>
        </svg>
        <span class="services__label">GAMIFICATION CLASSROOM</span>
      </li>
      <li class="services__item">
        <svg class="services__marker" viewBox="0 0 110 70" aria-hidden="true">
          <line x1="55" y1="0" x2="55" y2="15" stroke="#fff" stroke-width="1.5"/>
          <polygon points="55,15 100,35 55,55 10,35" fill="none" stroke="#fff" stroke-width="2"/>
          <rect x="46" y="29" width="14" height="10" fill="#fff"/>
          <rect x="61" y="31" width="5" height="9" fill="#fff"/>
        </svg>
        <span class="services__label">XAPI BLENDED LEARNING</span>
      </li>
    </ul>
  </section>

</main>
</body>
</html>
```